Dunmore Roofing

Want a professional looking business card

Industry/Entity Type

Business

Contact Information for Business Card

Paul Dunmore ( Owner) paul@dunmoreroofing-example.com, www.dunmoreroofing-example.com, Adress: 4172 Township road 43 Fernbrook,NL K9X4T2

```html
<!DOCTYPE html>
<html lang="en">
<head>
<meta charset="UTF-8">
<title>Dunmore Roofing – Business Card</title>
<link href="https://fonts.googleapis.com/css2?family=Open+Sans:wght@400;600;700&display=swap" rel="stylesheet">
<style>
  :root {
    --backdrop: #3b3532;
    --card: #252527;
    --brand-blue: #1f4f9e;
    --steel-grey: #8c8c90;
    --text-light: #f2f2f2;
  }
  * { box-sizing: border-box; margin: 0; padding: 0; }
  html, body {
    width: 1200px;
    height: 844px;
    overflow: hidden;
    background: var(--backdrop);
    font-family: "Open Sans", Arial, sans-serif;
  }
  .stage {
    position: relative;
    width: 1200px;
    height: 844px;
    display: flex;
    align-items: center;
    justify-content: center;
    gap: 50px;
  }
  .card {
    position: relative;
    width: 525px;
    height: 300px;
    background: var(--card);
    overflow: hidden;
    box-shadow: 0 10px 24px rgba(0,0,0,0.35);
  }

  /* Contact side */
  .card--contact .band {
    position: absolute;
    left: 0;
    width: 100%;
    height: 15px;
    background: var(--brand-blue);
  }
  .card--contact .band--top { top: 0; }
  .card--contact .band--bottom { bottom: 0; }
  .contact {
    position: absolute;
    inset: 15px 0;
    display: flex;
    flex-direction: column;
    align-items: center;
    justify-content: center;
    text-align: center;
    color: var(--text-light);
  }
  .contact__name {
    color: var(--brand-blue);
    font-size: 17px;
    font-weight: 400;
    letter-spacing: 0.3px;
    text-transform: uppercase;
  }
  .contact__role { font-size: 13px; margin-bottom: 20px; }
  .contact__address, .contact__online { font-size: 15px; line-height: 1.3; }
  .contact__address { margin-bottom: 18px; }

  /* Brand side */
  .tab {
    position: absolute;
    width: 30px;
    height: 36px;
    background: var(--brand-blue);
  }
  .tab::before {
    content: "";
    position: absolute;
    top: 0;
    width: 5px;
    height: 100%;
    background: var(--steel-grey);
  }
  .tab--top-right { top: 0; right: 0; }
  .tab--top-right::before { left: -9px; }
  .tab--left { top: 170px; left: 0; }
  .tab--left::before { right: -9px; }
  .brand {
    position: absolute;
    top: 96px;
    left: 0;
    width: 100%;
    display: flex;
    align-items: center;
    justify-content: center;
    gap: 12px;
  }
  .brand__mark {
    width: 22px;
    height: 22px;
    background: var(--brand-blue);
  }
  .brand__name {
    color: var(--brand-blue);
    font-size: 32px;
    font-weight: 700;
    letter-spacing: 3px;
    text-transform: uppercase;
  }
</style>
</head>
<body>
  <main class="stage">
    <section class="card card--contact">
      <div class="band band--top"></div>
      <div class="contact">
        <p class="contact__name">Paul Dunmore</p>
        <p class="contact__role">Owner</p>
        <p class="contact__address">4172 Township road 43<br>Fernbrook,NL K9X4T2</p>
        <p class="contact__online">paul@dunmoreroofing-example.com<br>www.dunmoreroofing-example.com</p>
      </div>
      <div class="band band--bottom"></div>
    </section>

    <section class="card card--brand">
      <div class="tab tab--top-right"></div>
      <div class="tab tab--left"></div>
      <div class="brand">
        <span class="brand__mark"></span>
        <span class="brand__name">Dunmore Roofing</span>
      </div>
    </section>
  </main>
</body>
</html>
```